FREE Network Assessment image for landing page

This graphic will be on a landing page and on the left will be Text and a download button that we change and control. The graphic for this project will be to the right.
I will add an example of the landing page area so that it makes more sense.

Please include the text from the sample - the font needs to be the same style as what we are using on the left side!

The graphic needs to be a .png file, roughly 713 x 527 white background. Use discretion on design layout.

Colors are black, Red = PMS 1795 and Gray = Cool Gray 10

Thanks,
Tom Garrick

Target Market(s)

small businesses

Industry/Entity Type

Information Technology

Font styles to use
Other font styles liked:
• See sample

Requirements
Must have
• see description
Nice to have
• Possibly small technology related image to help enhance the text but I don't want any image to compete with the text. Keep in mind the colors mentioned in the description - this is the web site colors.
Should not have
• Should not be hard to read

```html
<!DOCTYPE html>
<html lang="en">
<head>
<meta charset="utf-8">
<title>Free Network &amp; Computer Health Check</title>
<link rel="stylesheet" href="https://fonts.googleapis.com/css2?family=Archivo:wght@700;800;900&family=Roboto:wght@500;700&display=swap">
<style>
  :root {
    --frame-gray: #5e5a5b;
    --panel-gray: #5f5b5c;
    --text-gray: #555355;
    --brand-red: #e3262f;
    --brand-red-dark: #c8161d;
    --ink: #111111;
    --white: #ffffff;
  }
  * { margin: 0; padding: 0; box-sizing: border-box; }
  html, body {
    width: 1200px; height: 886px; overflow: hidden;
    background: var(--frame-gray);
  }
  .promo {
    position: absolute; left: 41px; top: 28px;
    width: 1120px; height: 828px;
    background: var(--white);
  }
  .headline {
    font-family: "Archivo", "Arial Black", sans-serif;
  }
  .headline span {
    position: absolute; left: 25px;
    display: block; line-height: 1; white-space: nowrap;
    transform-origin: left top;
  }
  .headline__free {
    top: 120px;
    font-size: 150px; font-weight: 900; color: var(--brand-red);
    letter-spacing: -2px;
    transform: scaleX(0.84);
  }
  .headline__sub {
    top: 270px;
    font-size: 52px; font-weight: 800;
    color: var(--text-gray); letter-spacing: -1px;
  }
  .headline__main {
    top: 324px;
    font-size: 68px; font-weight: 900;
    color: var(--brand-red); letter-spacing: -1.5px;
    transform: scaleX(0.9);
  }
  .headline__tail {
    top: 395px;
    font-size: 50px; font-weight: 800;
    color: var(--text-gray); letter-spacing: -1px;
  }
  .hero-art {
    position: absolute; left: 590px; top: 74px;
    width: 505px; height: 384px;
    background: radial-gradient(ellipse at 40% 50%, #3a3a3a 0%, #6d6d6d 40%, #d6d6d6 64%, #ffffff 74%);
  }
  .benefits {
    position: absolute; left: 25px; top: 466px;
    width: 1067px; height: 196px;
    background: var(--panel-gray);
    border: 2px solid var(--ink);
    box-shadow: 4px 4px 0 var(--ink);
    padding: 16px 0 0 30px;
    list-style: none;
    font-family: "Roboto", Arial, sans-serif;
    font-weight: 500; font-size: 21px; color: var(--white);
  }
  .benefits__item {
    display: flex; align-items: center; gap: 16px;
    height: 31px;
  }
  .benefits__tick { width: 18px; height: 18px; flex: none; }
  .cta {
    position: absolute; left: 33px; top: 672px;
    width: 831px; height: 64px;
    background: linear-gradient(var(--brand-red), var(--brand-red-dark));
    border: 3px solid var(--ink);
    border-radius: 0 0 26px 0;
    box-shadow: 3px 3px 0 #7a1014;
    display: flex; align-items: center; justify-content: center;
    font-family: "Archivo", Arial, sans-serif;
    font-weight: 800; font-size: 34px; color: var(--white);
    letter-spacing: 0.3px; text-decoration: none;
  }
</style>
</head>
<body>
  <main class="promo">
    <h1 class="headline">
      <span class="headline__free">FREE</span>
      <span class="headline__sub">Network &amp; Computer</span>
      <span class="headline__main">HEALTH CHECK</span>
      <span class="headline__tail">Service</span>
    </h1>

    <div class="hero-art" role="img" aria-label="Illustration of a glossy black globe with orbiting arrows beside a server tower with blue lights"></div>

    <ul class="benefits">
      <li class="benefits__item"><svg class="benefits__tick" viewBox="0 0 18 18"><rect x="1" y="4" width="12" height="12" fill="none" stroke="#fff" stroke-width="1.6"/><path d="M4 9.5l3 3 8-10" fill="none" stroke="#fff" stroke-width="2.4"/></svg>Check your network’s security against hacker attacks, theft, ransomware, viruses, and more.</li>
      <li class="benefits__item"><svg class="benefits__tick" viewBox="0 0 18 18"><rect x="1" y="4" width="12" height="12" fill="none" stroke="#fff" stroke-width="1.6"/><path d="M4 9.5l3 3 8-10" fill="none" stroke="#fff" stroke-width="2.4"/></svg>See who and what has access to your network and data.</li>
      <li class="benefits__item"><svg class="benefits__tick" viewBox="0 0 18 18"><rect x="1" y="4" width="12" height="12" fill="none" stroke="#fff" stroke-width="1.6"/><path d="M4 9.5l3 3 8-10" fill="none" stroke="#fff" stroke-width="2.4"/></svg>Perform network and Internet speed test</li>
      <li class="benefits__item"><svg class="benefits__tick" viewBox="0 0 18 18"><rect x="1" y="4" width="12" height="12" fill="none" stroke="#fff" stroke-width="1.6"/><path d="M4 9.5l3 3 8-10" fill="none" stroke="#fff" stroke-width="2.4"/></svg>Resolve PC slowness issues, security vulnerabilities and improper configurations</li>
      <li class="benefits__item"><svg class="benefits__tick" viewBox="0 0 18 18"><rect x="1" y="4" width="12" height="12" fill="none" stroke="#fff" stroke-width="1.6"/><path d="M4 9.5l3 3 8-10" fill="none" stroke="#fff" stroke-width="2.4"/></svg>Validate your backups are working and recoverable in a timely fashion.</li>
    </ul>

    <a class="cta" href="#">BOOK YOUR FREE APPOINTMENT NOW!</a>
  </main>
</body>
</html>
```